Marine Services Letterhead design

We need a letterhead design for an Australian owned company in Victoria named K+T Harbour Works Pty Ltd. We provide linesmen and launches to assist the large ships that come into port.
Our colour is orange.
The final design should have a strong nautical theme and communicate safety and reliability.
I would like to use the letter head on invoices so it should print to pdf well.

Target Market(s)

Owners and representatives of shipping companies. It is not for general public

Industry/Entity Type

Nautical

Requirements
Must have
• A shipping theme, not overly complicated, featuring safety orange colours but not all orange of course.
The letterhead should just sit at the top of the page so I can use for invoices.
Nice to have
• Something elegant and stylish
Should not have
• cartoons or pop art

```html
<!DOCTYPE html>
<html lang="en">
<head>
<meta charset="utf-8">
<title>K+T Harbour Works Pty Ltd — Letterhead</title>
<link rel="stylesheet" href="https://fonts.googleapis.com/css2?family=PT+Sans:wght@400;700&display=swap">
<style>
  :root {
    --paper: #ffffff;
    --brand-orange: #b5712f;
    --brand-orange-text: #b87a3a;
    --ink-black: #161412;
    --panel-grey: #f2f2f2;
    --mark-tan: #d9a466;
    --footer-text: #ffffff;
  }
  html, body {
    margin: 0;
    padding: 0;
    overflow: hidden;
    background: var(--paper);
  }
  .letterhead {
    position: relative;
    width: 926px;
    height: 1200px;
    background: var(--paper);
    overflow: hidden;
    font-family: "PT Sans", "Myriad Pro", sans-serif;
  }
  .brand-panel {
    position: absolute;
    left: 290px;
    top: 3px;
    width: 305px;
    height: 238px;
    background: var(--panel-grey);
  }
  .brand-square {
    position: absolute;
    left: 81px;
    top: 42px;
    width: 143px;
    height: 143px;
    background: var(--mark-tan);
  }
  .brand-name {
    position: absolute;
    left: 0;
    right: 0;
    top: 218px;
    margin: 0;
    text-align: center;
    font-size: 20px;
    font-weight: 700;
    color: var(--brand-orange-text);
    letter-spacing: 0.1px;
  }
  .footer-wave {
    position: absolute;
    left: 0;
    bottom: 0;
    width: 926px;
    height: 130px;
    display: block;
  }
  .contact-line {
    position: absolute;
    margin: 0;
    color: var(--footer-text);
    white-space: nowrap;
    display: flex;
    align-items: center;
  }
  .contact-line--phone {
    left: 548px;
    top: 1128px;
    font-size: 19px;
  }
  .contact-line--post {
    left: 599px;
    top: 1166px;
    font-size: 16px;
  }
  .contact-divider {
    display: inline-block;
    width: 1px;
    height: 20px;
    background: var(--footer-text);
    opacity: 0.7;
    margin: 0 7px;
  }
  .contact-icon {
    margin-right: 5px;
    fill: var(--footer-text);
  }
</style>
</head>
<body>
  <main class="letterhead">
    <header class="brand-panel">
      <div class="brand-square" aria-hidden="true"></div>
      <h1 class="brand-name">K+T Harbour Works Pty Ltd</h1>
    </header>

    <svg class="footer-wave" viewBox="0 0 926 130" aria-hidden="true">
      <path d="M0,118 C250,126 470,40 720,24 C820,18 885,32 926,52 L926,130 L0,130 Z" fill="var(--brand-orange)"/>
      <path d="M0,104 C250,112 470,30 720,12 C820,6 885,22 926,40" fill="none" stroke="var(--ink-black)" stroke-width="7"/>
      <path d="M0,8 C110,55 250,82 410,58" fill="none" stroke="var(--ink-black)" stroke-width="5"/>
      <path d="M0,78 C120,98 260,92 410,58" fill="none" stroke="var(--brand-orange)" stroke-width="2"/>
    </svg>

    <p class="contact-line contact-line--phone">
      <svg class="contact-icon" width="18" height="18" viewBox="0 0 24 24" aria-hidden="true">
        <circle cx="12" cy="12" r="10.5" fill="none" stroke="#fff" stroke-width="1.6"/>
        <path d="M8.6 6.8c.5-.4 1.1-.3 1.4.2l1 1.7c.3.5.1 1-.3 1.3l-.7.5c.5 1.4 1.4 2.6 2.6 3.5l.6-.6c.4-.4 1-.4 1.4-.1l1.6 1.1c.5.3.6 1 .2 1.4l-.8.9c-.6.6-1.6.7-2.4.3-2.8-1.5-4.9-4-5.9-7-.3-.8 0-1.7.6-2.3z"/>
      </svg>
      1300 555 014<span class="contact-divider"></span>ABN: 12345678901
    </p>
    <p class="contact-line contact-line--post">
      <svg class="contact-icon" width="12" height="18" viewBox="0 0 12 18" aria-hidden="true">
        <path d="M6 0C2.7 0 0 2.6 0 5.9 0 10.3 6 18 6 18s6-7.7 6-12.1C12 2.6 9.3 0 6 0zm0 8.3a2.4 2.4 0 1 1 0-4.8 2.4 2.4 0 0 1 0 4.8z"/>
      </svg>
      PO Box 214 Portside 3900
    </p>
  </main>
</body>
</html>
```